Fire Risk Assessment App needs a sleek UI design

I need a sleek, modern but professional design for my 5 page Fire Risk Assessment App. Include gradient background, fire themed colours including reds, yellows, light orange and a touch of black. Design must ooze simplicity and professionalism. This is for the UK market. See attached images and word doc for more information.

Target Market(s)

General public and business owners

Industry/Entity Type

Technology / Fire Safety

Colors
00AB8E
00BBA5
67D7C9
C6EFE9
E9F9F6
59FF00
82FF00
B8FF75
E3FFCB
F4FFEA
FFC000
F8CF3A
FAE287
FDF2CF
FEFAEE
F0912C
F2A743
F7CA91
FBE8D2
FDF5EE
EE7325
F08F49
F5BC92
FAE3D3
FDF4ED
EB3D1F
EC4F4E
F09395
F8D3D4
FCEDEE

```html
<!DOCTYPE html>
<html lang="en">
<head>
<meta charset="utf-8">
<title>Fire Risk Assessment App – Screens</title>
<link href="https://fonts.googleapis.com/css2?family=Lexend:wght@300;400;500&display=swap" rel="stylesheet">
<style>
:root{
  --page:#F2A743;
  --screen-top:#F6F3F0;
  --screen-bottom:#FBEAD6;
  --ink:#333333;
  --ink-soft:#555555;
  --ink-faint:#9a9a9a;
  --yellow:#F8CF3A;
  --yellow-deep:#E9B93A;
  --maroon:#A3000B;
  --red:#EC1C24;
  --fire-red:#EB3D1F;
  --green:#1FCB1A;
  --amber:#FFA50A;
  --orange:#F0912C;
  --gauge:#4C7A8C;
  --white:#FFFFFF;
  --nav-icon:#6f7880;
}
*{box-sizing:border-box;margin:0;padding:0}
html,body{width:1200px;height:727px;overflow:hidden}
body{background:var(--page);font-family:'Lexend',sans-serif;color:var(--ink);position:relative}
.screen{position:absolute;top:92px;width:262px;height:570px;border-radius:34px;overflow:hidden;
  background:linear-gradient(180deg,var(--screen-top) 0%,var(--screen-top) 35%,var(--screen-bottom) 100%)}
.screen--welcome{left:112px}
.screen--dashboard{left:482px}
.screen--support{left:850px}
.abs{position:absolute}
.center{left:0;right:0;text-align:center}

/* welcome */
.headline{top:40px;font-size:13.5px;line-height:18px;font-weight:400}
.preview-art{left:39px;top:90px;width:187px;height:162px;border-radius:6px;
  background:linear-gradient(160deg,#ffffff 0%,#fbeee0 70%,#f7ca91 100%)}
.tagline{top:262px;font-size:13.5px;line-height:18px;font-weight:300;color:var(--ink)}
.mic{top:305px;left:122px}
.btn{display:flex;align-items:center;border-radius:5px;font-size:12.5px}
.btn--create{left:28px;top:332px;width:209px;height:33px;
  background:linear-gradient(180deg,var(--yellow) 0%,var(--yellow-deep) 100%);color:#2a2a2a;
  box-shadow:0 3px 6px rgba(0,0,0,.15);padding-left:27px;gap:16px}
.btn--login{left:28px;top:418px;width:209px;height:33px;background:var(--maroon);color:var(--white);
  box-shadow:0 3px 6px rgba(0,0,0,.18);padding-left:27px;gap:42px}
.note{top:385px;font-size:13px;font-weight:300}
.fingerprint{left:113px;top:472px;width:39px;height:44px;border-radius:6px;
  background:linear-gradient(180deg,#ffffff,#ececec);box-shadow:0 1px 4px rgba(0,0,0,.12)}
.endorse{top:532px;font-size:10.5px;font-weight:300;color:var(--ink-soft)}

/* headers */
.page-title{top:40px;display:flex;align-items:center;justify-content:center;gap:6px;font-size:14px;font-weight:400;letter-spacing:.2px}

/* dashboard */
.start-label{top:77px;font-size:10px;font-weight:400}
.add-btn{left:109px;top:96px;width:44px;height:44px;border-radius:50%;background:var(--red)}
.type-art{width:42px;height:42px;border-radius:50%;background:radial-gradient(circle,#dfe6ee 0%,#ffffff 75%);
  box-shadow:0 1px 4px rgba(0,0,0,.12)}
.type-art--commercial{left:68px;top:167px}
.type-art--residential{left:154px;top:167px;background:radial-gradient(circle,#f5d6b8 0%,#ffffff 75%)}
.type-label{top:213px;width:90px;text-align:center;font-size:10px}
.status{left:28px;width:127px;height:27px;border-radius:4px;display:flex;align-items:center;
  justify-content:space-between;padding:0 8px 0 14px;color:var(--white);font-size:12.5px;font-weight:400}
.status--complete{top:247px;background:var(--green)}
.status--progress{top:323px;background:var(--amber)}
.status--purchases{top:414px;background:var(--red)}
.site{left:28px;top:285px;display:flex;align-items:center;gap:11px;font-size:13px}
.list{left:28px;list-style:none;font-size:11.2px;font-weight:300}
.list li{display:flex;align-items:center;gap:9px;height:20.5px;color:#222}
.list li::before{content:"";width:10px;height:10px;border:2.2px solid #111;border-radius:50%}
.list--progress{top:360px}
.list--purchases{top:450px}
.nav{left:0;right:0;bottom:0;height:44px;background:var(--white);border-radius:14px 14px 0 0;
  box-shadow:0 -2px 6px rgba(0,0,0,.05);display:flex;justify-content:space-around;align-items:center;padding:0 12px}

/* support */
.prompt{left:27px;top:92px;font-size:11px;font-weight:300;color:#222}
.prompt-mic{left:222px;top:88px}
.reply-box{left:27px;top:116px;width:207px;height:117px;background:var(--white);border-radius:3px;
  padding:10px 11px;font-size:8.5px;color:var(--ink-faint);font-weight:300}
</style>
</head>
<body>

<!-- Welcome screen -->
<section class="screen screen--welcome">
  <p class="abs center headline">The most 'user-friendly' Fire Risk<br>Assessment App available.</p>
  <div class="abs preview-art" role="img" aria-label="Stacked assessment question cards preview"></div>
  <p class="abs center tagline">Quick tap responses and<br>voice-activated typing.</p>
  <svg class="abs mic" width="18" height="20" viewBox="0 0 18 20" aria-hidden="true">
    <rect x="6" y="1" width="6" height="11" rx="3" fill="#8a8a8a"/>
    <path d="M3 9a6 6 0 0 0 12 0M9 15v4" stroke="#8a8a8a" stroke-width="1.6" fill="none"/>
  </svg>
  <div class="abs btn btn--create">
    <svg width="16" height="18" viewBox="0 0 16 18" aria-hidden="true"><circle cx="8" cy="5" r="3.8" fill="none" stroke="#333" stroke-width="1.3"/><path d="M1.5 17v-2a4 4 0 0 1 4-4h5a4 4 0 0 1 4 4v2z" fill="none" stroke="#333" stroke-width="1.3"/></svg>
    <span>Create a Free account</span>
  </div>
  <p class="abs center note">Any Responsible Person can do it.</p>
  <div class="abs btn btn--login">
    <svg width="16" height="16" viewBox="0 0 16 16" aria-hidden="true"><circle cx="8" cy="8" r="7" fill="none" stroke="#fff" stroke-width="1.2"/><path d="M3.5 8h7M8 5l3 3-3 3" fill="none" stroke="#fff" stroke-width="1.2"/></svg>
    <span>Customer Log in</span>
  </div>
  <div class="abs fingerprint" role="img" aria-label="Fingerprint sign-in"></div>
  <p class="abs center endorse">Created and endorsed by Veteran Fire Officers.</p>
</section>

<!-- Dashboard screen -->
<section class="screen screen--dashboard">
  <h1 class="abs center page-title">
    <svg width="24" height="24" viewBox="0 0 24 24" aria-hidden="true"><circle cx="12" cy="12" r="11" fill="#fff" stroke="var(--gauge)" stroke-width="2"/><path d="M5 14a7 7 0 0 1 14 0" fill="none" stroke="#F2A743" stroke-width="2"/><path d="M12 14l3-5" stroke="#333" stroke-width="1.5"/></svg>
    DASHBOARD
  </h1>
  <p class="abs center start-label">Start Fire Risk Assessment</p>
  <svg class="abs" style="left:0;top:0" width="262" height="200" aria-hidden="true">
    <line x1="118" y1="137" x2="98" y2="164" stroke="#333" stroke-width="1" stroke-dasharray="1.5 2.5"/>
    <line x1="144" y1="137" x2="168" y2="164" stroke="#333" stroke-width="1" stroke-dasharray="1.5 2.5"/>
  </svg>
  <div class="abs add-btn">
    <svg width="44" height="44" viewBox="0 0 44 44" aria-hidden="true"><path d="M22 10v24M10 22h24" stroke="#fff" stroke-width="4"/></svg>
  </div>
  <div class="abs type-art type-art--commercial" role="img" aria-label="Office building illustration"></div>
  <div class="abs type-art type-art--residential" role="img" aria-label="House illustration"></div>
  <span class="abs type-label" style="left:44px">Commercial</span>
  <span class="abs type-label" style="left:130px">Residential</span>

  <div class="abs status status--complete"><span>Complete</span>
    <svg width="13" height="13" viewBox="0 0 13 13" aria-hidden="true"><circle cx="6.5" cy="6.5" r="6.5" fill="#fff"/><path d="M3.5 6.8l2 2 4-4" stroke="var(--green)" stroke-width="1.6" fill="none"/></svg>
  </div>
  <div class="abs site">
    <svg width="27" height="26" viewBox="0 0 27 26" aria-hidden="true"><rect x="1" y="4" width="15" height="21" fill="#222"/><rect x="16" y="9" width="10" height="16" fill="#444"/><g fill="#fff"><rect x="3" y="7" width="2" height="2"/><rect x="7" y="7" width="2" height="2"/><rect x="11" y="7" width="2" height="2"/><rect x="3" y="12" width="2" height="2"/><rect x="7" y="12" width="2" height="2"/><rect x="11" y="12" width="2" height="2"/><rect x="3" y="17" width="2" height="2"/><rect x="7" y="17" width="2" height="2"/><rect x="11" y="17" width="2" height="2"/><rect x="19" y="12" width="2" height="2"/><rect x="19" y="17" width="2" height="2"/></g></svg>
    <span>Marlow Barbershop</span>
  </div>

  <div class="abs status status--progress"><span>In Progress</span>
    <svg width="14" height="14" viewBox="0 0 14 14" aria-hidden="true"><circle cx="7" cy="7" r="5.5" fill="none" stroke="#fff" stroke-width="2" stroke-dasharray="26 9"/></svg>
  </div>
  <ul class="abs list list--progress"><li>Elm Rd School</li><li>St Anne's Care Home</li></ul>

  <div class="abs status status--purchases"><span>Purchases</span>
    <svg width="17" height="15" viewBox="0 0 17 15" aria-hidden="true"><path d="M1 1h3l2 9h8l2-6H5" fill="none" stroke="#fff" stroke-width="1.6"/><circle cx="7" cy="13" r="1.4" fill="#fff"/><circle cx="13" cy="13" r="1.4" fill="#fff"/></svg>
  </div>
  <ul class="abs list list--purchases"><li>Residential Fire Risk Assessment</li><li>Commercial Fire Risk Assessment</li><li>Commercial Fire Risk Assessment</li></ul>

  <nav class="abs nav" aria-label="Main">
    <svg width="20" height="20" viewBox="0 0 24 24" aria-hidden="true"><circle cx="12" cy="12" r="11" fill="#fff" stroke="var(--gauge)" stroke-width="2"/><path d="M5 14a7 7 0 0 1 14 0" fill="none" stroke="#F2A743" stroke-width="2"/><path d="M12 14l3-5" stroke="#333" stroke-width="1.5"/></svg>
    <svg width="20" height="14" viewBox="0 0 20 14" aria-hidden="true"><rect width="20" height="14" rx="2" fill="var(--nav-icon)"/><rect y="3" width="20" height="3" fill="#fff"/><rect x="13" y="9" width="4" height="2" fill="#fff"/></svg>
    <svg width="18" height="17" viewBox="0 0 18 17" aria-hidden="true"><path d="M0 0h18v12H6l-4 4v-4H0z" fill="var(--nav-icon)"/><rect x="3" y="3" width="10" height="1.6" fill="#fff"/><rect x="3" y="6.5" width="7" height="1.6" fill="#fff"/></svg>
    <svg width="16" height="18" viewBox="0 0 16 18" aria-hidden="true"><rect x="3" y="1" width="11" height="16" fill="none" stroke="var(--nav-icon)" stroke-width="1.6"/><path d="M0 9h8M5 6l3 3-3 3" fill="none" stroke="var(--nav-icon)" stroke-width="1.6"/></svg>
  </nav>
</section>

<!-- Technical support screen -->
<section class="screen screen--support">
  <h1 class="abs center page-title">
    <svg width="18" height="18" viewBox="0 0 18 17" aria-hidden="true"><path d="M0 0h18v12H6l-4 4v-4H0z" fill="var(--orange)"/><rect x="3" y="3" width="10" height="1.6" fill="#fff"/><rect x="3" y="6.5" width="7" height="1.6" fill="#fff"/></svg>
    &nbsp;TECHNICAL SUPPORT
  </h1>
  <p class="abs prompt">Type/record your response here</p>
  <svg class="abs prompt-mic" width="14" height="20" viewBox="0 0 14 20" aria-hidden="true">
    <rect x="4" y="1" width="6" height="11" rx="3" fill="#8a8a8a"/>
    <path d="M1.5 9a5.5 5.5 0 0 0 11 0M7 15v4" stroke="#8a8a8a" stroke-width="1.6" fill="none"/>
  </svg>
  <div class="abs reply-box">Type here</div>

  <nav class="abs nav" aria-label="Main">
    <svg width="20" height="20" viewBox="0 0 24 24" aria-hidden="true"><circle cx="12" cy="12" r="11" fill="#fff" stroke="var(--gauge)" stroke-width="2"/><path d="M5 14a7 7 0 0 1 14 0" fill="none" stroke="#F2A743" stroke-width="2"/><path d="M12 14l3-5" stroke="#333" stroke-width="1.5"/></svg>
    <svg width="20" height="14" viewBox="0 0 20 14" aria-hidden="true"><rect width="20" height="14" rx="2" fill="var(--nav-icon)"/><rect y="3" width="20" height="3" fill="#fff"/><rect x="13" y="9" width="4" height="2" fill="#fff"/></svg>
    <svg width="18" height="17" viewBox="0 0 18 17" aria-hidden="true"><path d="M0 0h18v12H6l-4 4v-4H0z" fill="var(--nav-icon)"/><rect x="3" y="3" width="10" height="1.6" fill="#fff"/><rect x="3" y="6.5" width="7" height="1.6" fill="#fff"/></svg>
    <svg width="16" height="18" viewBox="0 0 16 18" aria-hidden="true"><rect x="3" y="1" width="11" height="16" fill="none" stroke="var(--nav-icon)" stroke-width="1.6"/><path d="M0 9h8M5 6l3 3-3 3" fill="none" stroke="var(--nav-icon)" stroke-width="1.6"/></svg>
  </nav>
</section>

</body>
</html>
```